Every Shelf Set Neatly or ESN Organized needs a business card design. ESN Organized is a professi

We need a business card design that is clean, sharp and conveys a sense of organization. I already have a logo.

Target Market(s)

Families (specifically mothers), small business owners, parents, seniors

Industry/Entity Type

Business

Contact Information for Business Card

My website is www.esnorganized-example.com and my Facebook page is http://www.sociallink-example.com/everyshelfsetneatly. The phone number is 418-552-7094 and I want to be listed as Lorna M. Pelham, Owner

Requirements
Must have
• My logo.

```html
<!DOCTYPE html>
<html lang="en">
<head>
<meta charset="utf-8">
<title>Every Shelf Set Neatly — Business Card</title>
<link href="https://fonts.googleapis.com/css2?family=Arimo:wght@400;700&family=Montserrat:wght@700&display=swap" rel="stylesheet">
<style>
  :root {
    --brand-blue: #0a7ddc;
    --paper-white: #f2f2f4;
    --ink-white: #ffffff;
    --backdrop: #e6e8eb;
    --card-shadow: rgba(20, 30, 45, 0.18);
  }
  * { margin: 0; padding: 0; box-sizing: border-box; }
  html, body {
    width: 1200px; height: 891px; overflow: hidden;
    background: var(--backdrop);
    font-family: "Arimo", Arial, sans-serif;
  }
  .canvas {
    width: 1200px; height: 891px;
    display: flex; align-items: center; justify-content: center; gap: 50px;
  }
  .card {
    width: 525px; height: 300px;
    position: relative; overflow: hidden;
    box-shadow: 0 10px 28px var(--card-shadow);
  }
  /* Front */
  .card-front { display: flex; background: var(--brand-blue); }
  .brand-band {
    width: 160px; height: 100%;
    background: var(--paper-white);
    padding: 44px 14px 0 18px;
  }
  .brand-name {
    display: flex; align-items: flex-start; gap: 10px;
    color: var(--brand-blue);
    font-family: "Arimo", Arial, sans-serif;
    font-weight: 400; font-size: 15px; line-height: 1.3;
  }
  .brand-square {
    width: 14px; height: 14px; flex: none; margin-top: 3px;
    background: var(--brand-blue);
  }
  .contact-side {
    flex: 1; padding: 48px 0 0 34px; color: var(--ink-white);
  }
  .person-name {
    font-family: "Montserrat", Arial, sans-serif;
    font-weight: 700; font-size: 25px; letter-spacing: 0.3px;
  }
  .person-title { font-size: 17px; margin-top: 2px; }
  .contact-list { list-style: none; margin-top: 22px; }
  .contact-item {
    display: flex; align-items: center; gap: 14px;
    font-size: 15px; margin-bottom: 10px; white-space: nowrap;
  }
  .contact-item.small { font-size: 12px; }
  .contact-icon {
    width: 22px; height: 22px; flex: none;
    background: var(--ink-white); color: var(--brand-blue);
    font-weight: 700; font-size: 14px;
    display: flex; align-items: center; justify-content: center;
  }
  /* Back */
  .card-back {
    background: var(--brand-blue); color: var(--ink-white);
    display: flex; flex-direction: column; align-items: center; justify-content: center;
    text-align: center;
  }
  .card-back .person-name { font-size: 22px; }
  .card-back .person-title { font-size: 16px; letter-spacing: 1px; margin-top: 0; }
</style>
</head>
<body>
<main class="canvas">
  <section class="card card-front" aria-label="Business card front">
    <div class="brand-band">
      <p class="brand-name"><span class="brand-square"></span><span>Every Shelf Set Neatly</span></p>
    </div>
    <div class="contact-side">
      <h1 class="person-name">Lorna M. Pelham</h1>
      <p class="person-title">Owner</p>
      <ul class="contact-list">
        <li class="contact-item"><span class="contact-icon">P</span>418 - 552 - 7094</li>
        <li class="contact-item"><span class="contact-icon">W</span>www.esnorganized-example.com</li>
        <li class="contact-item small"><span class="contact-icon">F</span>www.sociallink-example.com/everyshelfsetneatly</li>
      </ul>
    </div>
  </section>
  <section class="card card-back" aria-label="Business card back">
    <h2 class="person-name">Lorna M. Pelham</h2>
    <p class="person-title">Owner</p>
  </section>
</main>
</body>
</html>
```